Redesign Website - Current one too plain

The description is in the uploaded file. Please let me know if you need any more information. I'd prefer it if someone could implement the design to a WordPress site but the best design will win, regardless.
I would like the forms to look nice as well
UPDATE:
I don't think we can use the images that I provided, I think they make the site look a bit 'cheap' and I really don't know how to replace them. One thought I have had is to make the "Simple, Unique, Effective" a second feature on the right side of the page with the search on the left
Target Market(s)
Small companies, private sellers of cars and people who rent their caravan/holiday home out
Industry/Entity Type
Advertising
Number of Pages Required
3 page
Colors
Designer to choose colors to be used in the design.
Look and feel
Each slider illustrates characteristics of the customer's brand and the style your logo design should communicate.

```html
<!DOCTYPE html>
<html lang="en">
<head>
<meta charset="utf-8">
<title>Blotto – Create Your Advert</title>
<link href="https://fonts.googleapis.com/css2?family=Poppins:wght@400;500;600;700&display=swap" rel="stylesheet">
<style>
:root{
  --lime:#e5fb00;
  --ink:#2a2a2a;
  --muted:#9a9a9a;
  --band:#efefef;
  --field:#f1f1f1;
  --white:#ffffff;
  --rule:#dcdcdc;
}
*{box-sizing:border-box;margin:0;padding:0}
html,body{width:1200px;height:1169px;overflow:hidden;background:var(--white);font-family:'Poppins',sans-serif;color:var(--ink)}
.page{position:relative;width:1200px;height:1169px}
.site-header{position:absolute;top:0;left:0;width:1200px;height:101px}
.brand{position:absolute;left:89px;top:26px;font-weight:500;font-size:28px;letter-spacing:0;color:var(--ink)}
.main-nav{position:absolute;left:466px;top:33px;display:flex;align-items:center;font-size:12px;font-weight:500;text-transform:uppercase}
.nav-item{display:flex;align-items:center;gap:7px;padding:0 20px;border-left:1px solid #e4e4e4;height:26px}
.nav-item:first-child{border-left:0;padding-left:0}
.nav-item svg{width:17px;height:17px}
.cta{position:absolute;left:907px;top:23px;width:204px;height:43px;background:var(--lime);border-radius:4px;font-size:12px;font-weight:700;display:flex;align-items:center;justify-content:center;text-transform:uppercase}
.hero-band{position:absolute;top:101px;left:0;width:1200px;height:763px;background:var(--band)}
.hero-title{position:absolute;top:170px;width:1200px;text-align:center;font-size:40px;font-weight:700}
.perks{position:absolute;top:234px;width:1200px;display:flex;justify-content:center;gap:16px;font-size:13.5px}
.perk{display:flex;align-items:center;gap:9px}
.tick{width:28px;height:28px;border-radius:50%;background:var(--white);display:flex;align-items:center;justify-content:center}
.card{position:absolute;left:262px;top:308px;width:675px;height:706px;background:var(--white);border-radius:30px;border-bottom:3px solid var(--lime);box-shadow:0 20px 60px rgba(0,0,0,.06)}
.card-intro{position:absolute;top:36px;width:100%;text-align:center;font-size:13.5px}
.card-intro b{font-weight:600}
.field-label{position:absolute;font-size:10.5px;font-weight:500;text-transform:uppercase}
.field-label i{color:var(--lime);font-style:normal}
.field{position:absolute;background:var(--field);border-radius:6px}
.type-options{position:absolute;left:90px;top:165px;display:flex;gap:34px;font-size:12px;color:var(--muted)}
.type-options span{display:flex;align-items:center;gap:5px}
.type-options span::before{content:"";width:6px;height:6px;border:2px solid var(--ink);border-radius:50%}
.counter{position:absolute;right:90px;top:410px;font-size:12px;color:var(--muted)}
.upload{position:absolute;left:90px;top:449px;width:496px;height:137px;border:1.5px dashed #cfcfcf;border-radius:6px;text-align:center;font-size:12px;color:var(--muted);line-height:18px}
.upload-icon{width:39px;height:39px;margin:28px auto 12px;background:var(--ink);border-radius:5px;display:flex;align-items:center;justify-content:center}
.submit{position:absolute;left:270px;top:618px;width:136px;height:47px;background:var(--lime);border-radius:4px;font-weight:700;font-size:14px;display:flex;align-items:center;justify-content:center;border-bottom:2px solid #c8db00}
.footer-rule{position:absolute;left:89px;top:1105px;width:1022px;height:1px;background:var(--rule)}
.copyright{position:absolute;top:1124px;width:1200px;text-align:center;font-size:14px;font-weight:500}
.to-top{position:absolute;left:1136px;top:1085px;width:40px;height:40px;background:var(--ink);border-radius:4px;display:flex;align-items:center;justify-content:center}
</style>
</head>
<body>
<div class="page">
  <header class="site-header">
    <div class="brand">Blotto</div>
    <nav class="main-nav">
      <span class="nav-item"><svg viewBox="0 0 24 24"><path d="M12 3 2 12h3v8h5v-5h4v5h5v-8h3z" fill="#2a2a2a"/></svg>Home</span>
      <span class="nav-item"><svg viewBox="0 0 24 24" fill="none" stroke="#2a2a2a" stroke-width="1.6"><rect x="5" y="3" width="15" height="18" rx="1"/><circle cx="12.5" cy="10" r="2.5"/><path d="M8.5 17c1-2.5 7-2.5 8 0M3 7h3M3 12h3M3 17h3"/></svg>Contact</span>
      <span class="nav-item"><svg viewBox="0 0 24 24" fill="none" stroke="#2a2a2a" stroke-width="1.6"><circle cx="9" cy="7" r="4"/><path d="M2 21c0-5 4-8 9-8M14 20l1-3 6-6 2 2-6 6z"/></svg>Register</span>
      <span class="nav-item"><svg viewBox="0 0 24 24" fill="none" stroke="#2a2a2a" stroke-width="1.6"><circle cx="12" cy="7" r="4"/><path d="M4 21c0-5 4-7 8-7s8 2 8 7z"/></svg>Login</span>
    </nav>
    <div class="cta">Advertise your company</div>
  </header>

  <section class="hero-band"></section>
  <h1 class="hero-title">Create Your Advert</h1>
  <div class="perks">
    <div class="perk"><span class="tick"><svg width="14" height="12" viewBox="0 0 14 12"><path d="M1 6l4 4 8-9" fill="none" stroke="#e5fb00" stroke-width="2.4"/></svg></span>Free to advertise</div>
    <div class="perk"><span class="tick"><svg width="14" height="12" viewBox="0 0 14 12"><path d="M1 6l4 4 8-9" fill="none" stroke="#e5fb00" stroke-width="2.4"/></svg></span>Free graphics to print and display</div>
    <div class="perk"><span class="tick"><svg width="14" height="12" viewBox="0 0 14 12"><path d="M1 6l4 4 8-9" fill="none" stroke="#e5fb00" stroke-width="2.4"/></svg></span>Weatherproof vinyl graphics available</div>
  </div>

  <form class="card">
    <p class="card-intro"><b>Login</b> or <b>Register</b> to create your advert</p>
    <label class="field-label" style="left:89px;top:95px">Compan name, make/model of car, etc<i>*</i></label>
    <div class="field" style="left:90px;top:114px;width:496px;height:41px"></div>
    <div class="type-options"><span>Car</span><span>Company</span><span>Holiday</span></div>
    <label class="field-label" style="left:89px;top:209px">Town/city, county or area<i>*</i></label>
    <div class="field" style="left:90px;top:228px;width:244px;height:41px"></div>
    <label class="field-label" style="left:341px;top:209px">Website or social media page<i>*</i></label>
    <div class="field" style="left:342px;top:228px;width:244px;height:41px"></div>
    <label class="field-label" style="left:89px;top:292px">Description<i>*</i></label>
    <div class="field" style="left:90px;top:311px;width:496px;height:94px"></div>
    <span class="counter">0 of 4000 max characters</span>
    <label class="field-label" style="left:89px;top:428px">Upload photo</label>
    <div class="upload">
      <div class="upload-icon"><svg width="20" height="20" viewBox="0 0 20 20" fill="none" stroke="#e5fb00" stroke-width="2"><path d="M10 13V3M6 7l4-4 4 4M3 12v5h14v-5"/></svg></div>
      Upload images - select main image first<br>Maximum Upload size: 10 MB
    </div>
    <div class="submit">SUBMIT</div>
  </form>

  <div class="footer-rule"></div>
  <p class="copyright">© Copyright 2023 Blotto. All Rights Reserved</p>
  <div class="to-top"><svg width="10" height="7" viewBox="0 0 10 7"><path d="M1 6l4-4 4 4" fill="none" stroke="#e5fb00" stroke-width="1.8"/></svg></div>
</div>
</body>
</html>
```